Velmarotix - world unique technology for better life - please let them know who am i at first sight

We need a new business card for company which is a provider of unique crystal based technology suitable for all living being. For more information and final design you can use our brochure (our colours are black and blue from brochure).
We use Verdana font

Industry/Entity Type

Business

Contact Information for Business Card

regular dimension

Font styles to use
Other font styles liked:
• Verdana

Requirements
Must have
• Logo
• name
• function/position
• phone
• mobile
• e-mail
• adress
Nice to have
• inovative design (technology directed)

```html
<!DOCTYPE html>
<html lang="en">
<head>
<meta charset="utf-8">
<title>Velmarotix business card</title>
<link rel="stylesheet" href="https://fonts.googleapis.com/css2?family=Noto+Sans:wght@400;700&display=swap">
<style>
  :root {
    --page: #ececec;
    --card: #3b3b3d;
    --card-edge: #2e2e30;
    --blue: #1cb8e8;
    --blue-soft: #5fd0f2;
    --ink: #0b0b0b;
    --text: #f2f2f2;
  }
  * { box-sizing: border-box; margin: 0; padding: 0; }
  html, body {
    width: 1200px; height: 1200px; overflow: hidden;
    background: var(--page);
    font-family: Verdana, "Noto Sans", sans-serif;
  }
  .sheet {
    width: 1200px; height: 1200px;
    display: flex; flex-direction: column; align-items: center; justify-content: center;
    gap: 60px;
  }
  .card {
    position: relative;
    width: 840px; height: 480px;
    background: linear-gradient(135deg, var(--card) 0%, var(--card-edge) 100%);
    border-radius: 16px;
    overflow: hidden;
    box-shadow: 0 10px 24px rgba(0,0,0,0.18);
  }
  .pattern {
    position: absolute;
    border-radius: 50%;
  }
  .card--front .pattern {
    left: 300px; top: -70px; width: 420px; height: 620px;
    background: radial-gradient(ellipse at 60% 50%, var(--blue) 0%, rgba(28,184,232,0.75) 45%, rgba(28,184,232,0) 72%);
  }
  .card--back .pattern {
    left: 170px; top: -40px; width: 380px; height: 560px;
    background: radial-gradient(ellipse at 55% 50%, var(--ink) 0%, rgba(11,11,11,0.7) 45%, rgba(11,11,11,0) 72%);
  }
  .brand {
    position: absolute;
    display: flex; align-items: center; gap: 18px;
  }
  .brand__dot {
    width: 74px; height: 74px; border-radius: 50%;
    background: var(--blue);
    flex: none;
  }
  .brand__name {
    font-size: 40px; font-weight: 400; letter-spacing: 1px;
    text-transform: uppercase;
  }
  .card--front .brand { left: 200px; top: 200px; }
  .card--front .brand__name { color: var(--blue-soft); }
  .card--back .brand { left: 80px; top: 80px; }
  .card--back .brand__name { color: var(--ink); }

  .contact {
    position: absolute; left: 440px; top: 170px;
    color: var(--text);
  }
  .contact__name {
    color: var(--blue); font-weight: 700; font-size: 26px; letter-spacing: 1px;
    text-transform: uppercase;
  }
  .contact__role { font-size: 20px; margin-top: 2px; }
  .contact__address { font-size: 20px; line-height: 1.25; margin-top: 24px; }
  .contact__list { list-style: none; margin-top: 24px; font-size: 17px; }
  .contact__list li { display: flex; align-items: center; gap: 12px; height: 30px; }
  .contact__list svg { width: 16px; height: 16px; fill: var(--blue); flex: none; }
</style>
</head>
<body>
<main class="sheet">
  <section class="card card--front" aria-label="Card front">
    <div class="pattern" role="img" aria-label="Blue crystal lattice sphere pattern breaking into fragments"></div>
    <div class="brand">
      <span class="brand__dot"></span>
      <span class="brand__name">Velmarotix</span>
    </div>
  </section>

  <section class="card card--back" aria-label="Card back">
    <div class="pattern" role="img" aria-label="Black crystal lattice sphere pattern breaking into fragments"></div>
    <div class="brand">
      <span class="brand__dot"></span>
      <span class="brand__name">Velmarotix</span>
    </div>
    <div class="contact">
      <p class="contact__name">Daren Holt</p>
      <p class="contact__role">Managing Director</p>
      <p class="contact__address">Unit 7, Larkfield Road,<br>Marlow, OR 97321</p>
      <ul class="contact__list">
        <li>
          <svg viewBox="0 0 16 16" aria-hidden="true"><path d="M3.5 1l3 3-1.6 1.8c.8 1.8 2.2 3.2 4 4L10.7 8l3 3-1.8 2.4C6.5 13.4 2.6 9.5 2.6 3.6z"/></svg>
          <span>+1 555 014 2387</span>
        </li>
        <li>
          <svg viewBox="0 0 16 16" aria-hidden="true"><path d="M4.5 1h7a1 1 0 0 1 1 1v12a1 1 0 0 1-1 1h-7a1 1 0 0 1-1-1V2a1 1 0 0 1 1-1zm.5 2v9h6V3zm3 10a.8.8 0 1 0 0 .01z"/></svg>
          <span>+1 555 018 6621</span>
        </li>
        <li>
          <svg viewBox="0 0 16 16" aria-hidden="true"><path d="M1 3h14v10H1zm1.5 1.3V5l5.5 3.6L13.5 5v-.7L8 7.6z"/></svg>
          <span>darenholt@mail.com</span>
        </li>
      </ul>
    </div>
  </section>
</main>
</body>
</html>
```